New career and executive coaching business needs a business card design including logo

Company name: 'Bramblefield Growth Partners.' The aim of my coaching engagements is to help people improve their communication in the workplace and achieve their career goals. The process involves working with individuals to help them uncover their strengths and talents, then leverage those to improve their working lives. The Tarwick Inventory is the starting point to the process. I am after an exciting and interesting business card design (including logo)which is professional yet will still get people's attention.

Industry/Entity Type

Business

Contact Information for Business Card

Name: Malcolm Dervaney
Position: Owner
Address: 58 Quorrin Ct, Elmbridge Vic 3190
Phone: 0418923047
Website: bramblefieldgrowth.com.au
Email: malcolm@bgp.com.au

Colors
33a6d7
00a990
0355a3
3176b5

Requirements
Must have
• logo

```html
<!DOCTYPE html>
<html lang="en">
<head>
<meta charset="utf-8">
<title>Bramblefield Growth Partners – Business Card</title>
<link rel="stylesheet" href="https://fonts.googleapis.com/css2?family=Oswald:wght@500&family=Open+Sans:wght@400;700&display=swap">
<style>
  :root {
    --backdrop: #2e2824;
    --card: #141414;
    --card-edge: #0b0b0b;
    --ink: #ffffff;
    --ink-soft: #c9c9c9;
    --rule: #3a3a3a;
  }
  * { box-sizing: border-box; margin: 0; padding: 0; }
  html, body {
    width: 1200px; height: 844px; overflow: hidden;
    background: var(--backdrop);
  }
  .stage {
    position: relative; width: 1200px; height: 844px;
    display: flex; align-items: center; justify-content: center; gap: 60px;
  }
  .card {
    position: relative; width: 520px; height: 298px;
    background: var(--card);
    border: 1px solid var(--card-edge);
    box-shadow: 0 10px 28px rgba(0,0,0,.45);
    color: var(--ink);
  }
  .brand { display: flex; align-items: center; }
  .brand-disc { background: var(--ink); border-radius: 50%; flex: none; }
  .brand-name {
    font-family: 'Oswald', sans-serif; font-weight: 500; color: var(--ink);
    text-transform: uppercase; line-height: 1.05;
  }
  .brand-name .primary { display: block; letter-spacing: .5px; }
  .brand-name .secondary { display: block; letter-spacing: .3px; }

  /* contact side */
  .card-contact .brand { position: absolute; left: 30px; top: 118px; }
  .card-contact .brand-disc { width: 62px; height: 62px; margin-right: 12px; }
  .card-contact .primary { font-size: 22px; }
  .card-contact .secondary { font-size: 9.5px; }
  .divider {
    position: absolute; left: 296px; top: 0; bottom: 0;
    border-left: 1px solid var(--rule);
  }
  .details {
    position: absolute; left: 318px; top: 58px;
    font-family: 'Open Sans', sans-serif; color: var(--ink-soft);
    font-size: 12.5px; line-height: 1.4;
  }
  .details .person { font-weight: 700; font-size: 15.5px; color: var(--ink); }
  .details .role { font-size: 11.5px; margin-bottom: 14px; }
  .details .address { margin-bottom: 14px; }
  .contact-list { list-style: none; }
  .contact-list li { display: flex; align-items: center; gap: 8px; }
  .contact-list svg { width: 10px; height: 10px; fill: var(--ink); flex: none; }

  /* logo side */
  .card-front { display: flex; align-items: center; justify-content: center; }
  .card-front .brand-disc { width: 84px; height: 84px; margin-right: 16px; }
  .card-front .primary { font-size: 30px; }
  .card-front .secondary { font-size: 12.5px; }
</style>
</head>
<body>
<main class="stage">
  <section class="card card-contact">
    <div class="brand">
      <span class="brand-disc"></span>
      <span class="brand-name">
        <span class="primary">Bramblefield</span>
        <span class="secondary">Growth Partners</span>
      </span>
    </div>
    <div class="divider"></div>
    <div class="details">
      <p class="person">Malcolm Dervaney</p>
      <p class="role">Owner</p>
      <p class="address">58 Quorrin Ct, Elmbridge<br>Vic 3190</p>
      <ul class="contact-list">
        <li>
          <svg viewBox="0 0 10 10" aria-hidden="true"><path d="M2 0.5l1.6 2.2-1 1c.6 1.3 1.5 2.2 2.7 2.7l1-1L8.5 7 7.6 9C4 8.6 1.2 5.8 0.6 2z"/></svg>
          0418923047
        </li>
        <li>
          <svg viewBox="0 0 10 10" aria-hidden="true"><path d="M0 2h10v0.8L5 6 0 2.8z"/><path d="M0 4l5 3.2L10 4v4H0z"/></svg>
          malcolm@bgp.com.au
        </li>
        <li>
          <svg viewBox="0 0 10 10" aria-hidden="true"><circle cx="5" cy="5" r="4.6"/></svg>
          bramblefieldgrowth.com.au
        </li>
      </ul>
    </div>
  </section>

  <section class="card card-front">
    <div class="brand">
      <span class="brand-disc"></span>
      <span class="brand-name">
        <span class="primary">Bramblefield</span>
        <span class="secondary">Growth Partners</span>
      </span>
    </div>
  </section>
</main>
</body>
</html>
```